Modern 6 page design, business card, and a banner

I need a website design for my CFO service. The service uses proprietary tech, so it needs to be modern. I also need business card and banner design to match the site.
The banner size is 33.75 X 79.25.
I'm open to colors and styles.

Target Market(s)

Startups

Coding

Coded - Design and coding required

Number of Pages Required

5+ page

```html
<!DOCTYPE html>
<html lang="en">
<head>
<meta charset="utf-8">
<title>Ledgra – Strategic Financial Planner</title>
<link href="https://fonts.googleapis.com/css2?family=Lato:wght@300;400;700&family=Montserrat:wght@500;700;800&display=swap" rel="stylesheet">
<style>
:root{
  --navy:#29254f;
  --navy-deep:#1e1b3d;
  --ink:#1b1b1f;
  --text:#2d2d33;
  --muted:#d6d6dc;
  --grey-band:#ebebed;
  --dark:#15171c;
  --red:#bf4f47;
  --orange:#df8f3e;
  --yellow:#d8b23b;
  --blue:#5aa6cf;
  --accent:#d05a5a;
  --white:#ffffff;
}
*{margin:0;padding:0;box-sizing:border-box}
html,body{width:1200px;height:4068px;overflow:hidden}
body{position:relative;font-family:"Lato",sans-serif;color:var(--text);background:var(--white)}
.section{position:absolute;left:0;width:1200px;overflow:hidden}
.abs{position:absolute}

/* header */
.site-header{top:0;height:118px;background:var(--navy)}
.brand{left:122px;top:34px;text-align:center;color:var(--white)}
.brand-name{font-family:"Lato",sans-serif;font-weight:300;font-size:40px;line-height:1;letter-spacing:1px}
.brand-tag{font-size:8px;color:var(--accent);margin-top:6px;letter-spacing:.3px}
.nav{top:70px;left:0;font-family:"Montserrat",sans-serif;font-weight:500;font-size:19px;color:var(--white)}
.nav a{position:absolute;white-space:nowrap;color:var(--white);text-decoration:none}
.nav a.active{color:#b9b7c9}
.social-top{top:22px}
.social-dot{position:absolute;width:16px;height:16px;border-radius:3px;background:var(--white)}
.call{left:870px;top:14px;color:var(--white);font-family:"Montserrat",sans-serif;font-size:14px;display:flex;align-items:center;gap:10px}
.call strong{font-size:21px;font-weight:500}

/* hero */
.hero{top:118px;height:561px}
.hero-photo{position:absolute;inset:0;background:linear-gradient(100deg,#3c4148 0%,#2f3a42 35%,#4a5860 60%,#56656b 80%,#3d4a52 100%)}
.hero-shade{position:absolute;inset:0;background:rgba(20,22,30,.35)}
.hero-title{left:0;width:1200px;top:190px;text-align:center;font-family:"Lato",sans-serif;font-weight:700;font-size:74px;color:var(--white);line-height:1}
.hero-copy{left:0;width:1200px;top:290px;text-align:center;font-size:20px;line-height:33px;color:var(--white)}
.btn-light{left:507px;top:376px;width:186px;height:57px;background:var(--white);color:var(--ink);font-family:"Montserrat",sans-serif;font-weight:500;font-size:21px;display:flex;align-items:center;justify-content:center}
.slider-arrow{top:272px;width:50px;height:50px;border-radius:50%;background:var(--white)}

/* welcome */
.welcome{top:679px;height:493px}
.section-title{font-family:"Montserrat",sans-serif;font-weight:700;color:var(--ink);white-space:nowrap}
.welcome-title{left:114px;top:100px;font-size:55px;display:flex;align-items:baseline;gap:22px}
.welcome-title .brand-word{font-family:"Lato",sans-serif;font-weight:300;font-size:64px}
.tick-list{left:110px;width:640px}
.tick-item{position:absolute;left:0;padding-left:46px;font-size:15px;line-height:27.5px}
.tick-item svg{position:absolute;left:0;top:0}
.welcome-photo{left:750px;top:105px;width:346px;height:360px;border-radius:50%;background:radial-gradient(circle at 40% 45%,#c9d6de 0%,#8fa8ba 35%,#3f6f95 70%,#27476a 100%)}

/* why */
.why{top:1172px;height:442px;background:var(--grey-band)}
.why-title{left:0;width:1200px;top:118px;text-align:center;font-size:37px}
.why-copy{left:182px;width:876px;top:208px;text-align:center;font-size:15px;line-height:31px}

/* visualize */
.visualize{top:1614px;height:612px}
.vis-title{left:112px;top:86px;font-size:36px;line-height:46px}
.btn-dark{left:109px;top:452px;width:131px;height:44px;background:var(--navy);color:var(--white);font-size:15px;display:flex;align-items:center;justify-content:center;border-radius:2px}
.phone{left:813px;top:52px;width:256px;height:524px;border-radius:26px;background:#f2f3f6;border:2px solid #d8dae0}
.phone-screen{position:absolute;left:10px;top:46px;right:10px;bottom:46px;border-radius:6px;background:linear-gradient(180deg,#241f66 0%,#1c1a4d 55%,#2a1f55 100%)}

/* how */
.how{top:2226px;height:1153px;background:radial-gradient(ellipse at 70% 30%,#23272f 0%,#16181d 55%,#0f1014 100%)}
.how-title{left:0;width:1200px;top:104px;text-align:center;font-size:38px;color:var(--white)}
.how-copy{left:80px;width:1040px;top:184px;text-align:center;font-size:15px;line-height:32px;color:var(--white)}
.step{left:702px;width:400px;color:var(--white)}
.step h3{font-family:"Montserrat",sans-serif;font-weight:700;font-size:23px;margin-bottom:8px}
.step p{font-size:14.5px;line-height:25px;color:#e4e4ea}

/* contact */
.contact{top:3379px;height:619px}
.contact-title{left:0;width:1200px;top:68px;text-align:center;font-size:38px}
.contact-sub{left:0;width:1200px;top:128px;text-align:center;font-size:18px}
.form-box{left:109px;top:230px;width:407px;height:319px;border:2px solid #3b4a9a;background:#f4f4f6}
.field{position:absolute;height:33px;border:1px solid #9aa0b8;background:var(--white);font-size:12px;padding:10px 14px;color:#333}
.submit{left:159px;top:253px;width:100px;height:32px;background:var(--navy);color:var(--white);font-size:12px;font-weight:700;display:flex;align-items:center;justify-content:center;outline:2px solid var(--navy);outline-offset:2px}
.info-icon{left:616px;width:72px;height:72px;border-radius:50%;background:var(--navy);display:flex;align-items:center;justify-content:center}
.info-text{left:715px;font-size:18px;color:var(--ink);line-height:27px}
.info-text small{font-size:14px}
.social-bottom .social-dot{width:24px;height:24px;background:var(--navy);border-radius:3px}

/* footer */
.site-footer{top:3998px;height:70px;background:var(--navy)}
.copyright{left:110px;top:25px;color:var(--white);font-size:14px}
</style>
</head>
<body>

<header class="section site-header">
  <div class="abs brand">
    <div class="brand-name">Ledgra</div>
    <div class="brand-tag">Strategic Financial Planner</div>
  </div>
  <div class="abs social-top">
    <span class="social-dot" style="left:622px"></span>
    <span class="social-dot" style="left:674px"></span>
    <span class="social-dot" style="left:729px"></span>
    <span class="social-dot" style="left:786px"></span>
  </div>
  <div class="abs call">
    <svg width="22" height="22" viewBox="0 0 24 24"><path fill="#fff" d="M6.6 10.8a15.1 15.1 0 0 0 6.6 6.6l2.2-2.2c.3-.3.7-.4 1-.2 1.1.4 2.3.6 3.6.6.6 0 1 .4 1 1V20c0 .6-.4 1-1 1A17 17 0 0 1 3 4c0-.6.4-1 1-1h3.5c.6 0 1 .4 1 1 0 1.3.2 2.5.6 3.6.1.3 0 .7-.2 1z"/></svg>
    <span>Call : <strong>555-014-2277</strong></span>
  </div>
  <nav class="abs nav">
    <a class="active" style="left:313px">Home</a>
    <a style="left:425px">About Us</a>
    <a style="left:564px">Services</a>
    <a style="left:698px">Visual Finance for Mobile</a>
    <a style="left:981px">Contact Us</a>
  </nav>
</header>

<section class="section hero">
  <div class="hero-photo" role="img" aria-label="Businessman drawing a financial chart over a city skyline"></div>
  <div class="hero-shade"></div>
  <h1 class="abs hero-title">LEDGRA</h1>
  <p class="abs hero-copy">Lorem ipsum dolor sit amet, consectetur adipiscing elit<br>sed do eiusmod tempor incididunt ut labore et dolore magna aliqua.</p>
  <a class="abs btn-light">Get started</a>
  <div class="abs slider-arrow" style="left:113px">
    <svg width="50" height="50" viewBox="0 0 50 50"><path d="M34 25H16M23 17l-8 8 8 8" stroke="#111" stroke-width="4" fill="none" stroke-linecap="round" stroke-linejoin="round"/></svg>
  </div>
  <div class="abs slider-arrow" style="left:1038px">
    <svg width="50" height="50" viewBox="0 0 50 50"><path d="M16 25h18M27 17l8 8-8 8" stroke="#111" stroke-width="4" fill="none" stroke-linecap="round" stroke-linejoin="round"/></svg>
  </div>
</section>

<section class="section welcome">
  <h2 class="abs section-title welcome-title">Welcome To <span class="brand-word">Ledgra</span></h2>
  <div class="abs tick-list" style="top:200px">
    <div class="tick-item" style="top:0">
      <svg width="32" height="32" viewBox="0 0 32 32"><circle cx="16" cy="16" r="13" fill="none" stroke="#29254f" stroke-width="2.5" stroke-dasharray="70 12"/><path d="M10 16l5 5 11-12" stroke="#29254f" stroke-width="2.5" fill="none" stroke-linecap="round"/></svg>
      Small businesses can visualize their finances, have a plan they trust and monitor progress daily. No more waiting for the latest monthly or quarterly report from your accountant. No more late nights digging through spreadsheets to figure out where you really stand. No more wondering if you're prepared for the future.
    </div>
    <div class="tick-item" style="top:137px">
      <svg width="32" height="32" viewBox="0 0 32 32"><circle cx="16" cy="16" r="13" fill="none" stroke="#29254f" stroke-width="2.5" stroke-dasharray="70 12"/><path d="M10 16l5 5 11-12" stroke="#29254f" stroke-width="2.5" fill="none" stroke-linecap="round"/></svg>
      Ledgra delivers a clear financial plan tailored to your goals, an easy mobile dashboard to track progress on a daily basis and all the professional advice and support you need along the way.
    </div>
  </div>
  <div class="abs welcome-photo" role="img" aria-label="Hand holding a smartphone over a laptop showing financial charts"></div>
</section>

<section class="section why">
  <h2 class="abs section-title why-title">Why Ledgra Visual Finance?</h2>
  <p class="abs why-copy">Small businesses shouldn't be forced to choose between the strategic value of traditional financial services and the convenience of modern mobile reporting technology. With Ledgra, you have access to decades of financial planning experience and a daily view into real finance reports - all delivered through a mobile app you can take with you on the road, in the field, on the shop floor or wherever you need to be.</p>
</section>

<section class="section visualize">
  <h2 class="abs section-title vis-title">Visualize your finances in real time</h2>
  <div class="abs tick-list" style="top:183px;width:655px">
    <div class="tick-item" style="top:0;padding-left:56px">
      <svg width="32" height="32" viewBox="0 0 32 32"><circle cx="16" cy="16" r="13" fill="none" stroke="#29254f" stroke-width="2.5" stroke-dasharray="70 12"/><path d="M10 16l5 5 11-12" stroke="#29254f" stroke-width="2.5" fill="none" stroke-linecap="round"/></svg>
      <span style="line-height:29px;display:block">Ledgra delivers an easy-to-understand dashboard using our own mobile app, customized for your business and your specific plan. Relying on clean data and mirroring your actual financial statements, Ledgra lets you see what a CFO sees and always be confident you're looking at real numbers.</span>
    </div>
    <div class="tick-item" style="top:157px;padding-left:56px">
      <svg width="32" height="32" viewBox="0 0 32 32"><circle cx="16" cy="16" r="13" fill="none" stroke="#29254f" stroke-width="2.5" stroke-dasharray="70 12"/><path d="M10 16l5 5 11-12" stroke="#29254f" stroke-width="2.5" fill="none" stroke-linecap="round"/></svg>
      <span style="line-height:29px;display:block">Monitor results daily, understand where you stand versus plan and make better decisions with Ledgra Mobile.</span>
    </div>
  </div>
  <a class="abs btn-dark">Read More</a>
  <div class="abs phone">
    <div class="phone-screen" role="img" aria-label="Mobile finance dashboard with a line chart and bar charts"></div>
  </div>
</section>

<section class="section how">
  <h2 class="abs section-title how-title">How it Works</h2>
  <p class="abs how-copy">Ledgra combines traditional bookkeeping and “outsourced CFO” services with a customizable visual finance mobile app. We provide everything needed to develop a plan, clean and structure your accounting data and launch your visual finance dashboard.</p>

  <svg class="abs" style="left:0;top:0" width="1200" height="1153" viewBox="0 0 1200 1153">
    <g fill="none" stroke="#e8e8ec" stroke-width="1.5">
      <polyline points="281,566 414,387 497,387"/>
      <polyline points="324,608 379,546 497,546"/>
      <polyline points="349,684 497,684"/>
      <polyline points="327,758 379,813 497,813"/>
      <polyline points="284,793 415,987 502,987"/>
    </g>
    <path d="M589 305a82 82 0 0 1 0 164z" fill="#bf4f47"/>
    <path d="M589 458a82 82 0 0 1 0 164z" fill="#df8f3e"/>
    <path d="M589 602a82 82 0 0 1 0 164z" fill="#d8b23b"/>
    <path d="M589 747a82 82 0 0 1 0 164z" fill="#28264a"/>
    <path d="M589 900a82 82 0 0 1 0 164z" fill="#5aa6cf"/>
    <g fill="#fff">
      <circle cx="592" cy="387" r="50"/>
      <circle cx="592" cy="540" r="50"/>
      <circle cx="592" cy="684" r="50"/>
      <circle cx="592" cy="829" r="50"/>
      <circle cx="592" cy="982" r="50"/>
    </g>
    <g fill="none" stroke="#1b1b1f" stroke-width="2.2" stroke-linecap="round" stroke-linejoin="round">
      <polyline points="570,402 584,386 596,394 614,372"/><polyline points="604,372 614,372 614,382"/>
      <circle cx="588" cy="536" r="14"/><line x1="598" y1="546" x2="610" y2="558"/>
      <circle cx="592" cy="684" r="9"/><circle cx="592" cy="684" r="18" stroke-dasharray="6 5"/>
      <rect x="570" y="812" width="40" height="28" rx="2"/><polyline points="576,832 586,822 594,828 604,818"/>
      <path d="M580 960h20l8 8v32h-28z"/><line x1="586" y1="976" x2="602" y2="976"/><line x1="586" y1="986" x2="602" y2="986"/>
    </g>
    <circle cx="205" cy="682" r="95" fill="#29254f" stroke="#fff" stroke-width="6"/>
    <text x="205" y="690" text-anchor="middle" font-family="Lato, sans-serif" font-weight="300" font-size="34" fill="#fff">Ledgra</text>
    <text x="205" y="712" text-anchor="middle" font-family="Lato, sans-serif" font-size="8" fill="#d05a5a">Strategic Financial Planner</text>
    <circle cx="268" cy="586" r="12" fill="#a55a52"/>
    <circle cx="306" cy="629" r="12" fill="#df8f3e"/>
    <circle cx="322" cy="684" r="12" fill="#d8b23b"/>
    <circle cx="306" cy="737" r="12" fill="#28264a"/>
    <circle cx="268" cy="777" r="12" fill="#4d9ccb"/>
  </svg>

  <div class="abs step" style="top:325px"><h3>Develop Plan</h3><p>we work with you to develop a 3 to 5 year financial plan tailored to your business goals.</p></div>
  <div class="abs step" style="top:487px"><h3>Clean Data</h3><p>our bookkeepers clean your historical data, set-up live data intake, and ensure alignment with finance reports</p></div>
  <div class="abs step" style="top:632px"><h3>Visual Finances</h3><p>we launch your customized visual finance dashboard on Ledgra Mobile</p></div>
  <div class="abs step" style="top:785px"><h3>Monitor Daily</h3><p>you monitor real financial results against plan on a daily basis</p></div>
  <div class="abs step" style="top:933px"><h3>Advise Monthly</h3><p>our financial experts provide support and help respond as your business grows</p></div>
</section>

<section class="section contact">
  <h2 class="abs section-title contact-title">Contact Us</h2>
  <p class="abs contact-sub">Contact us to learn more about Ledgra.</p>
  <form class="abs form-box">
    <div class="field" style="left:18px;top:58px;width:173px">Name</div>
    <div class="field" style="left:209px;top:58px;width:175px">Phone Number</div>
    <div class="field" style="left:18px;top:110px;width:366px">E-mail</div>
    <div class="field" style="left:18px;top:160px;width:366px;height:75px">Enter Your Message</div>
    <div class="abs submit">SUBMIT</div>
  </form>

  <div class="abs info-icon" style="top:227px">
    <svg width="26" height="30" viewBox="0 0 24 28"><path d="M12 1a9 9 0 0 0-9 9c0 7 9 17 9 17s9-10 9-17a9 9 0 0 0-9-9z" fill="none" stroke="#fff" stroke-width="2"/><circle cx="12" cy="10" r="3.5" fill="#fff"/></svg>
  </div>
  <div class="abs info-text" style="top:236px">2240 Harbor Lane, Floor 3, Westbrook<br>Ohio 44020 &nbsp;<small>UNITED STATES</small></div>

  <div class="abs info-icon" style="top:314px">
    <svg width="30" height="22" viewBox="0 0 30 22"><rect x="1" y="1" width="28" height="20" rx="2" fill="none" stroke="#fff" stroke-width="2"/><polyline points="1,2 15,13 29,2" fill="none" stroke="#fff" stroke-width="2"/></svg>
  </div>
  <div class="abs info-text" style="top:336px">hello@ledgra.com</div>

  <div class="abs info-icon" style="top:401px">
    <svg width="24" height="24" viewBox="0 0 24 24"><path fill="#fff" d="M6.6 10.8a15.1 15.1 0 0 0 6.6 6.6l2.2-2.2c.3-.3.7-.4 1-.2 1.1.4 2.3.6 3.6.6.6 0 1 .4 1 1V20c0 .6-.4 1-1 1A17 17 0 0 1 3 4c0-.6.4-1 1-1h3.5c.6 0 1 .4 1 1 0 1.3.2 2.5.6 3.6.1.3 0 .7-.2 1z"/></svg>
  </div>
  <div class="abs info-text" style="top:423px;left:720px">555-014-2277</div>

  <div class="abs social-bottom" style="top:513px;left:0">
    <span class="social-dot" style="left:632px"></span>
    <span class="social-dot" style="left:705px"></span>
    <span class="social-dot" style="left:784px"></span>
    <span class="social-dot" style="left:845px"></span>
  </div>
</section>

<footer class="section site-footer">
  <p class="abs copyright">© 2019 Copyrights Company Name | All Rights Reserved</p>
</footer>

</body>
</html>
```